Before the kettle boils, pocast with content in its majority of technology

Page dedicated to a pocast with content in its majority of technology. The page also contains the chapters of the podcast (pluggin vocalink) will also contain news. Preferably Worpress. There is already a very basic page with a simple theme, the logo and little more, I would like something more professional. Www.lamparadebolsillo.com The logo does not want to change.

Target Market(s)

Anyone

Colors

Designer to choose colors to be used in the design.

Requirements
Must have
• You can put the vocalink pluggin with the podcast chapters

```html
<!DOCTYPE html>
<html lang="en">
<head>
<meta charset="utf-8">
<title>Before the kettle boils – Podcast de tecnología</title>
<link rel="stylesheet" href="https://fonts.googleapis.com/css2?family=Oswald:wght@400;500&family=Open+Sans:wght@400;600&display=swap">
<style>
:root{
  --orange:#f47a20;
  --orange-deep:#e0631a;
  --ink:#222;
  --text:#555;
  --muted:#777;
  --line:#e2e2e2;
  --hero-dark:#141414;
  --footer:#2b2826;
  --footer-bottom:#1c1a19;
  --white:#fff;
}
*{box-sizing:border-box;margin:0;padding:0}
html,body{width:1200px;height:2871px;overflow:hidden}
body{position:relative;background:var(--white);font-family:"Open Sans",Arial,sans-serif;color:var(--text)}
.abs{position:absolute}

/* Hero */
.hero{left:0;top:0;width:1200px;height:643px;background:radial-gradient(ellipse at 72% 45%,#4a4a4a 0%,#262626 35%,var(--hero-dark) 75%)}
.brand-box{left:36px;top:0;width:250px;height:195px;background:#1b1b1b;display:flex;flex-direction:column;align-items:center;justify-content:center;gap:6px}
.brand-mark{width:58px;height:58px;border-radius:50%;background:var(--orange)}
.brand-name{font-family:"Oswald",sans-serif;font-weight:500;font-size:17px;color:var(--orange);letter-spacing:.3px}
.brand-tag{font-family:"Oswald",sans-serif;font-size:11px;color:#ddd;letter-spacing:.5px;margin-top:-4px}
.topbar{left:736px;top:36px;display:flex;align-items:center;gap:10px;color:#fff;font-size:19px}
.lang{border:1.5px solid #ddd;border-radius:14px;padding:1px 10px;font-size:14px;margin-left:12px}
.social-sq{width:22px;height:22px;border-radius:3px}
.nav{left:398px;top:94px;display:flex;font-size:15px;color:#fff;text-transform:uppercase}
.nav span{margin-right:38px}
.nav .active{color:var(--orange)}
.hero-title{left:96px;top:298px;font-family:"Oswald",sans-serif;font-weight:400;font-size:44px;color:#fff;line-height:1}
.hero-sub{left:96px;top:352px;font-family:"Oswald",sans-serif;font-weight:400;font-size:29px;color:#fff;line-height:1}
.btn-play{left:96px;top:414px;width:153px;height:52px;border-radius:26px;background:var(--orange);color:#fff;font-family:"Oswald",sans-serif;font-size:19px;display:flex;align-items:center;justify-content:center}
.slider-arrows{left:1057px;top:570px;display:flex;gap:4px}
.slider-arrows div{width:26px;height:32px;background:#0b0b0b;display:flex;align-items:center;justify-content:center}

/* Articles */
.section-title{left:90px;top:694px;font-size:24px;color:var(--ink);font-weight:600;letter-spacing:.3px}
.card{left:88px;width:717px;border:1px solid var(--line);background:#fff}
.card-title{position:absolute;left:18px;top:20px;font-size:18px;font-weight:400;color:var(--ink)}
.card-share{position:absolute;right:22px;top:24px;display:flex;gap:6px}
.card-share i{display:block;width:15px;height:15px;border-radius:2px;background:#3a7bc8}
.card-share i:last-child{background:#d9463a}
.card-meta{position:absolute;left:18px;top:51px;font-size:13px;color:var(--muted)}
.card-meta b{font-weight:400;margin:0 12px}
.card-text{position:absolute;left:18px;top:78px;width:680px;font-size:13.5px;line-height:23px;color:var(--muted)}
.player{position:absolute;left:13px;top:143px;width:689px;height:257px}
.player-top{position:absolute;right:18px;top:14px;display:flex;gap:22px}
.controls{position:absolute;left:204px;bottom:36px;display:flex;align-items:center;gap:26px;color:#fff;font-size:14px}
.ctrl-play{width:70px;height:70px;border-radius:50%;background:var(--orange-deep);display:flex;align-items:center;justify-content:center}
.progress{position:absolute;left:0;bottom:0;width:100%;height:7px;background:#111}
.progress span{display:block;height:100%;background:var(--orange)}
.load-more{left:382px;top:2470px;width:130px;height:38px;border:1.5px solid var(--orange);border-radius:19px;color:var(--orange);font-size:13px;display:flex;align-items:center;justify-content:center}

/* Sidebar */
.side-box{left:824px;width:287px;border:1px solid var(--line);background:#fff}
.side-head{height:40px;background:var(--orange);color:#fff;font-size:15px;padding:10px 20px;text-transform:uppercase}
.blog-item{display:flex;gap:12px;margin:0 18px;padding:16px 0 14px;border-bottom:1px solid #eee}
.blog-item:last-child{border-bottom:none}
.thumb{width:80px;height:56px;flex:none;border:3px solid #fff;box-shadow:0 0 0 1px #ddd}
.blog-item h4{font-size:13px;font-weight:400;color:var(--ink)}
.blog-item p{font-size:11px;line-height:16px;color:var(--muted)}
.tw-head{display:flex;justify-content:space-between;align-items:center;padding:16px 18px 10px;font-size:18px;color:var(--ink);border-bottom:1px solid #eee}
.follow{width:56px;height:18px;border:1px solid #bbb;border-radius:3px;background:#f3f3f3;font-size:10px;text-align:center;line-height:16px;color:#333}
.tweet{padding:16px 18px 14px;border-bottom:1px solid #eee;width:268px}
.tweet-row{display:flex;gap:12px;align-items:center;margin-bottom:8px}
.avatar{width:56px;height:44px;flex:none;background:linear-gradient(135deg,#555,#999)}
.tweet-name{font-size:15px;font-weight:400;color:var(--ink)}
.tweet-handle{font-size:12px;color:var(--muted)}
.tweet p{font-size:11px;line-height:18px;color:var(--muted)}
.scrollbar{position:absolute;right:4px;top:58px;width:10px;height:160px;background:#c9c9c9}
.loc-title{left:828px;top:2008px;font-size:18px;font-weight:400;color:var(--ink);text-transform:uppercase}
.map{left:827px;top:2043px;width:288px;height:295px;background:linear-gradient(160deg,#e9e9e9,#d6d6d6)}

/* Footer */
.footer{left:0;top:2562px;width:1200px;height:223px;background:var(--footer);color:#ddd}
.f-col{position:absolute;top:40px}
.f-col h5{font-size:15px;font-weight:400;color:#fff;text-transform:uppercase;margin-bottom:22px}
.f-col p,.f-col li{font-size:12px;line-height:20px;color:#cfcfcf}
.f-col ul{list-style:none}
.f-col li{line-height:24px}
.f-col li::before{content:"▸ ";font-size:9px}
.news-form{display:flex;margin-top:14px}
.news-input{width:140px;height:30px;background:#fff;font-size:12px;color:#999;padding:6px 10px}
.news-btn{width:60px;height:30px;background:var(--orange);color:#fff;font-size:12px;text-align:center;line-height:30px}
.f-social{display:flex;gap:12px;margin-top:16px}
.f-social i{display:block;width:32px;height:32px;border-radius:50%;border:1.5px solid #ccc}
.bottom-bar{left:0;top:2785px;width:1200px;height:86px;background:var(--footer-bottom);color:#ddd;font-size:12px;text-align:center;line-height:86px}
</style>
</head>
<body>

<header>
  <div class="abs hero" role="img" aria-label="Studio microphone in front of dark acoustic foam"></div>
  <div class="abs brand-box">
    <div class="brand-mark"></div>
    <div class="brand-name">BEFORE THE KETTLE BOILS</div>
    <div class="brand-tag">PODCAST DE TECNOLOGIA</div>
  </div>
  <div class="abs topbar">
    <svg width="18" height="18" viewBox="0 0 18 18"><rect width="18" height="18" rx="3" fill="#f47a20"/><path d="M5 4l2.5 0 1 3-1.5 1a7 7 0 0 0 3 3l1-1.5 3 1v2.5a1 1 0 0 1-1 1A10 10 0 0 1 4 5a1 1 0 0 1 1-1z" fill="#fff"/></svg>
    <span>(08) 5550 1842</span>
    <span class="lang">EN ⌄</span>
    <i class="social-sq" style="background:#2d8ad6"></i>
    <i class="social-sq" style="background:#2aa4df"></i>
    <i class="social-sq" style="background:#2478b4"></i>
    <i class="social-sq" style="background:#d9463a"></i>
  </div>
  <nav class="abs nav">
    <span class="active">Home</span><span>About us</span><span>Article</span><span>Projects</span><span>Blog</span><span>Support</span><span>Contact us</span>
  </nav>
  <h1 class="abs hero-title">BEFORE THE KETTLE BOILS</h1>
  <p class="abs hero-sub">Neque porro quisquam est qui dolorem</p>
  <div class="abs btn-play">PLAY NOW</div>
  <div class="abs slider-arrows">
    <div><svg width="10" height="16"><path d="M8 2L2 8l6 6" stroke="#fff" stroke-width="2" fill="none"/></svg></div>
    <div><svg width="10" height="16"><path d="M2 2l6 6-6 6" stroke="#fff" stroke-width="2" fill="none"/></svg></div>
  </div>
</header>

<main>
  <h2 class="abs section-title">LATEST ARTICLE</h2>

  <article class="abs card" style="top:740px;height:425px">
    <h3 class="card-title">A free soundwell for phones</h3>
    <div class="card-share"><i></i><i></i><i></i><i></i></div>
    <div class="card-meta">Author : admin<b>|</b>Post id : 12365<b>|</b>Post on : October 1, 2017</div>
    <p class="card-text">Today chapter dedicated to the lovers of the series and the films. It is the streaming video service of the website lumino.tv portal dedicated to learning English through the method of watching movies and series</p>
    <div class="player" role="img" aria-label="Phone playing music on a wooden table with earphones" style="background:linear-gradient(120deg,#6b3a1c,#a8592a 50%,#4a2814)">
      <div class="player-top"><svg width="16" height="14"><path d="M8 13L2 7a3.5 3.5 0 0 1 6-4 3.5 3.5 0 0 1 6 4z" fill="#fff"/></svg><svg width="16" height="14"><path d="M1 3h4l6 8h4M1 11h4l6-8h4" stroke="#fff" stroke-width="2" fill="none"/></svg></div>
      <div class="controls"><span>1:22</span><svg width="16" height="16"><rect x="1" y="2" width="3" height="12" fill="#fff"/><path d="M15 2v12L5 8z" fill="#fff"/></svg><div class="ctrl-play"><svg width="24" height="28"><path d="M3 2v24l20-12z" fill="#fff"/></svg></div><svg width="16" height="16"><path d="M1 2v12l10-6z" fill="#fff"/><rect x="12" y="2" width="3" height="12" fill="#fff"/></svg><span>-4:08</span><svg width="20" height="16" style="margin-left:150px"><path d="M1 5h4l5-4v14l-5-4H1z" fill="#fff"/><path d="M13 4a5 5 0 0 1 0 8M16 2a8 8 0 0 1 0 12" stroke="#fff" stroke-width="1.6" fill="none"/></svg></div>
      <div class="progress"><span style="width:33%"></span></div>
    </div>
  </article>

  <article class="abs card" style="top:1170px;height:424px">
    <h3 class="card-title">Security in your Mail</h3>
    <div class="card-share"><i></i><i></i><i></i><i></i></div>
    <div class="card-meta">Author : admin<b>|</b>Post id : 12365<b>|</b>Post on : October 1, 2017</div>
    <p class="card-text">Today chapter dedicated to the lovers of the series and the films. It is the streaming video service of the website lumino.tv portal dedicated to learning English through the method of watching movies and series</p>
    <div class="player" role="img" aria-label="Hands holding a phone in a dim room" style="background:linear-gradient(110deg,#2a2a2a,#5a3a3a 50%,#2d2d2d)">
      <div class="player-top"><svg width="16" height="14"><path d="M8 13L2 7a3.5 3.5 0 0 1 6-4 3.5 3.5 0 0 1 6 4z" fill="#fff"/></svg><svg width="16" height="14"><path d="M1 3h4l6 8h4M1 11h4l6-8h4" stroke="#fff" stroke-width="2" fill="none"/></svg></div>
      <div class="controls"><span>1:22</span><svg width="16" height="16"><rect x="1" y="2" width="3" height="12" fill="#fff"/><path d="M15 2v12L5 8z" fill="#fff"/></svg><div class="ctrl-play"><svg width="24" height="28"><path d="M3 2v24l20-12z" fill="#fff"/></svg></div><svg width="16" height="16"><path d="M1 2v12l10-6z" fill="#fff"/><rect x="12" y="2" width="3" height="12" fill="#fff"/></svg><span>-4:08</span><svg width="20" height="16" style="margin-left:150px"><path d="M1 5h4l5-4v14l-5-4H1z" fill="#fff"/><path d="M13 4a5 5 0 0 1 0 8M16 2a8 8 0 0 1 0 12" stroke="#fff" stroke-width="1.6" fill="none"/></svg></div>
      <div class="progress"><span style="width:16%"></span></div>
    </div>
  </article>

  <article class="abs card" style="top:1598px;height:422px">
    <h3 class="card-title">Notekeep, that's what I do</h3>
    <div class="card-share"><i></i><i></i><i></i><i></i></div>
    <div class="card-meta">Author : admin<b>|</b>Post id : 12365<b>|</b>Post on : October 1, 2017</div>
    <p class="card-text">Today chapter dedicated to the lovers of the series and the films. It is the streaming video service of the website lumino.tv portal dedicated to learning English through the method of watching movies and series</p>
    <div class="player" role="img" aria-label="White earbuds over a green sound waveform" style="background:linear-gradient(180deg,#25232b 55%,#3f6a3a 100%)">
      <div class="player-top"><svg width="16" height="14"><path d="M8 13L2 7a3.5 3.5 0 0 1 6-4 3.5 3.5 0 0 1 6 4z" fill="#fff"/></svg><svg width="16" height="14"><path d="M1 3h4l6 8h4M1 11h4l6-8h4" stroke="#fff" stroke-width="2" fill="none"/></svg></div>
      <div class="controls"><span>1:22</span><svg width="16" height="16"><rect x="1" y="2" width="3" height="12" fill="#fff"/><path d="M15 2v12L5 8z" fill="#fff"/></svg><div class="ctrl-play"><svg width="24" height="28"><path d="M3 2v24l20-12z" fill="#fff"/></svg></div><svg width="16" height="16"><path d="M1 2v12l10-6z" fill="#fff"/><rect x="12" y="2" width="3" height="12" fill="#fff"/></svg><span>-4:08</span><svg width="20" height="16" style="margin-left:150px"><path d="M1 5h4l5-4v14l-5-4H1z" fill="#fff"/><path d="M13 4a5 5 0 0 1 0 8M16 2a8 8 0 0 1 0 12" stroke="#fff" stroke-width="1.6" fill="none"/></svg></div>
      <div class="progress"><span style="width:51%"></span></div>
    </div>
  </article>

  <article class="abs card" style="top:2027px;height:418px">
    <h3 class="card-title">Do you like series? Do you know lumino.tv?</h3>
    <div class="card-share"><i></i><i></i><i></i><i></i></div>
    <div class="card-meta">Author : admin<b>|</b>Post id : 12365<b>|</b>Post on : October 1, 2017</div>
    <p class="card-text">Today chapter dedicated to the lovers of the series and the films. It is the streaming video service of the website lumino.tv portal dedicated to learning English through the method of watching movies and series</p>
    <div class="player" role="img" aria-label="Abstract purple and yellow wave lines on a dark blue background" style="background:linear-gradient(100deg,#1a1440,#5a2f8a 45%,#8a4ab0 60%,#16123a)">
      <div class="player-top"><svg width="16" height="14"><path d="M8 13L2 7a3.5 3.5 0 0 1 6-4 3.5 3.5 0 0 1 6 4z" fill="#fff"/></svg><svg width="16" height="14"><path d="M1 3h4l6 8h4M1 11h4l6-8h4" stroke="#fff" stroke-width="2" fill="none"/></svg></div>
      <div class="controls"><span>1:22</span><svg width="16" height="16"><rect x="1" y="2" width="3" height="12" fill="#fff"/><path d="M15 2v12L5 8z" fill="#fff"/></svg><div class="ctrl-play"><svg width="24" height="28"><path d="M3 2v24l20-12z" fill="#fff"/></svg></div><svg width="16" height="16"><path d="M1 2v12l10-6z" fill="#fff"/><rect x="12" y="2" width="3" height="12" fill="#fff"/></svg><span>-4:08</span><svg width="20" height="16" style="margin-left:150px"><path d="M1 5h4l5-4v14l-5-4H1z" fill="#fff"/><path d="M13 4a5 5 0 0 1 0 8M16 2a8 8 0 0 1 0 12" stroke="#fff" stroke-width="1.6" fill="none"/></svg></div>
      <div class="progress"><span style="width:26%"></span></div>
    </div>
  </article>

  <div class="abs load-more">LOAD MORE</div>
</main>

<aside>
  <section class="abs side-box" style="top:740px;height:770px">
    <div class="side-head">Latest Blog</div>
    <div class="blog-item"><div class="thumb" role="img" aria-label="Blog thumbnail" style="background:linear-gradient(135deg,#6a6a7a,#c9c2c0)"></div><div><h4>This is a sample Post 1</h4><p>Lorem ipsum dolor sit amet, consectetuer adipiscing elit,</p></div></div>
    <div class="blog-item"><div class="thumb" role="img" aria-label="Blog thumbnail" style="background:linear-gradient(135deg,#3a4250,#8a8c90)"></div><div><h4>This is a sample Post 1</h4><p>Lorem ipsum dolor sit amet, consectetuer adipiscing elit,</p></div></div>
    <div class="blog-item"><div class="thumb" role="img" aria-label="Blog thumbnail" style="background:linear-gradient(135deg,#2a2a2a,#6a5a4a)"></div><div><h4>This is a sample Post 1</h4><p>Lorem ipsum dolor sit amet, consectetuer adipiscing elit,</p></div></div>
    <div class="blog-item"><div class="thumb" role="img" aria-label="Blog thumbnail" style="background:linear-gradient(135deg,#7a5a4a,#c8a890)"></div><div><h4>This is a sample Post 1</h4><p>Lorem ipsum dolor sit amet, consectetuer adipiscing elit,</p></div></div>
    <div class="blog-item"><div class="thumb" role="img" aria-label="Blog thumbnail" style="background:linear-gradient(135deg,#4a3020,#8a6040)"></div><div><h4>This is a sample Post 1</h4><p>Lorem ipsum dolor sit amet, consectetuer adipiscing elit,</p></div></div>
    <div class="blog-item"><div class="thumb" role="img" aria-label="Blog thumbnail" style="background:linear-gradient(135deg,#3a3a3a,#b08060)"></div><div><h4>This is a sample Post 1</h4><p>Lorem ipsum dolor sit amet, consectetuer adipiscing elit,</p></div></div>
    <div class="blog-item"><div class="thumb" role="img" aria-label="Blog thumbnail" style="background:linear-gradient(135deg,#c07a6a,#e8c0b0)"></div><div><h4>This is a sample Post 1</h4><p>Lorem ipsum dolor sit amet, consectetuer adipiscing elit,</p></div></div>
    <div class="blog-item"><div class="thumb" role="img" aria-label="Blog thumbnail" style="background:linear-gradient(135deg,#1f2a30,#4a5a60)"></div><div><h4>This is a sample Post 1</h4><p>Lorem ipsum dolor sit amet, consectetuer adipiscing elit,</p></div></div>
  </section>

  <section class="abs side-box" style="top:1525px;height:450px;overflow:hidden">
    <div class="tw-head"><span>Chirper Updates</span><span class="follow">Follow</span></div>
    <div class="scrollbar"></div>
    <div class="tweet"><div class="tweet-row"><div class="avatar" role="img" aria-label="Profile image"></div><div><div class="tweet-name">Beforethekettleboils</div><div class="tweet-handle">@MaraKettle</div></div></div><p>Lorem ipsum dolor sit amet, consectetur ading elit, sed do eiusmod tempor incidi-</p></div>
    <div class="tweet"><div class="tweet-row"><div class="avatar" role="img" aria-label="Profile image"></div><div><div class="tweet-name">Beforethekettleboils</div><div class="tweet-handle">@MaraKettle</div></div></div><p>Lorem ipsum dolor sit amet, consectetur ading elit, sed do eiusmod tempor incidi-</p></div>
    <div class="tweet" style="border-bottom:none"><div class="tweet-row"><div class="avatar" role="img" aria-label="Profile image"></div><div><div class="tweet-name">Beforethekettleboils</div><div class="tweet-handle">@MaraKettle</div></div></div><p>Lorem ipsum dolor sit amet, consectetur ading elit, sed do eiusmod tempor incidi-</p></div>
  </section>

  <h3 class="abs loc-title">Location</h3>
  <div class="abs map" role="img" aria-label="Street map showing the studio location"></div>
  <svg class="abs" style="left:929px;top:2150px" width="28" height="38" viewBox="0 0 28 38"><path d="M14 1a13 13 0 0 0-13 13c0 10 13 23 13 23s13-13 13-23A13 13 0 0 0 14 1z" fill="#e25a5a"/><circle cx="14" cy="14" r="5" fill="#fff"/></svg>
</aside>

<footer>
  <div class="abs footer">
    <div class="f-col" style="left:88px;width:290px">
      <h5>Before the kettle boils</h5>
      <p>HostWeave helps you to quickly and easily build incredible websites with PageLoom.</p>
      <p style="margin-top:14px">Proin gravida nibh vel velit auctor aliquet. Aenean sollicitudin, lorem quis bibendum auctor, nisi elit consequat ipsum, nec sagit-</p>
    </div>
    <div class="f-col" style="left:435px">
      <h5>Links</h5>
      <ul><li>Customer Support</li><li>Documentation</li><li>Resources</li><li>General FAQs</li><li>Shortcodes</li></ul>
    </div>
    <div class="f-col" style="left:650px;width:200px">
      <h5>Get in touch</h5>
      <p>Address : 12 Willow Lane,<br>Brookfield, NJ</p>
      <p style="margin-top:12px">Phone : 201 555 0147</p>
      <p style="margin-top:12px">Email : hello@kettlecast.com</p>
    </div>
    <div class="f-col" style="left:905px;width:210px">
      <h5>Newsletter</h5>
      <p>Your about us information would fit here nicely.</p>
      <div class="news-form"><div class="news-input">Email address</div><div class="news-btn">Submit</div></div>
      <div class="f-social"><i></i><i></i><i></i></div>
    </div>
  </div>
  <div class="abs bottom-bar">Copyright © 2017. All Rights Reserved</div>
</footer>

</body>
</html>
```